Flyer for the Lumen 2025 Conference

I am looking to produce a flyer for our upcoming conference, Lumen 2025. This is an annual conference that we plan to publicize on social media. The ideal designer will create a flyer that is eye-catching and effectively communicates the key information. Please see attached our logo, speaker photo, and flyer content.

Target Market(s)

All demographics

Industry/Entity Type

Christian

Font styles to use
Sans Serif

Requirements
Should not have
• Cross, church

```html
<!DOCTYPE html>
<html lang="en">
<head>
<meta charset="utf-8">
<title>Lumen 2025 Conference Flyer</title>
<link rel="stylesheet" href="https://fonts.googleapis.com/css2?family=Saira+Condensed:ital,wght@0,300;0,400;0,600;0,800;1,800;1,900&family=Saira:wght@400;500&display=swap">
<style>
  :root {
    --stage: #7aa5ea;
    --navy: #0d3b66;
    --navy-deep: #072b4f;
    --navy-mid: #14497c;
    --ink: #050b14;
    --white: #ffffff;
    --paper: #eef0f4;
    --orange: #f07a1a;
    --badge-edge: #8a95a5;
  }
  * { box-sizing: border-box; margin: 0; padding: 0; }
  html, body { width: 1200px; height: 900px; overflow: hidden; }
  body { background: var(--stage); font-family: "Saira Condensed", sans-serif; }

  .flyer {
    position: absolute; left: 280px; top: 20px;
    width: 640px; height: 860px;
    background: var(--navy); overflow: hidden; color: var(--white);
  }
  .flyer-backdrop { position: absolute; inset: 0; }

  .speaker-photo {
    position: absolute; left: 70px; top: 120px; width: 330px; height: 500px;
    background: linear-gradient(160deg, #2b7fd6 0%, #1b5fae 45%, #0e2f58 100%);
    border-radius: 0 0 60px 0;
  }

  .brand-mark {
    position: absolute; left: 34px; top: 34px; width: 100px; height: 100px;
    background: var(--navy); border: 1px solid rgba(255,255,255,.35);
    display: flex; align-items: center; justify-content: center;
    font-family: "Saira", sans-serif; font-weight: 500; font-size: 19px; color: var(--white);
    letter-spacing: .5px;
  }

  .event-title {
    position: absolute; right: 40px; top: 118px; text-align: right;
    font-weight: 300; line-height: .92; text-transform: uppercase;
  }
  .event-title .year { font-size: 56px; display: block; }
  .event-title .kind { font-size: 48px; display: block; }
  .event-title .label { font-size: 34px; display: block; }

  .topic {
    position: absolute; right: 36px; top: 300px; text-align: right;
    font-weight: 900; font-style: italic; text-transform: uppercase; line-height: .86;
  }
  .topic .tag { font-size: 22px; color: var(--orange); font-weight: 800; margin-right: 6px; vertical-align: 40px; }
  .topic .line { font-size: 92px; display: block; }
  .topic .outline { color: transparent; -webkit-text-stroke: 2px var(--white); }

  .speaker-card {
    position: absolute; left: 40px; top: 560px; width: 390px; height: 110px;
    background: linear-gradient(180deg, var(--white), var(--paper));
    border-radius: 0 60px 0 60px;
    color: var(--navy); padding: 20px 0 0 44px;
  }
  .speaker-card .role { font-size: 18px; font-weight: 600; letter-spacing: 14px; text-transform: uppercase; }
  .speaker-card .name { font-size: 34px; font-weight: 800; text-transform: uppercase; line-height: 1.1; }

  .contact {
    position: absolute; left: 40px; top: 682px; width: 240px;
    font-family: "Saira", sans-serif; font-size: 15px; line-height: 1.3;
  }
  .contact .heading { font-size: 14px; margin-bottom: 3px; }
  .contact .row { display: flex; align-items: center; gap: 8px; margin-bottom: 3px; }
  .contact svg { width: 15px; height: 15px; flex: none; }
  .contact .app-note { font-size: 12px; line-height: 1.2; margin-top: 6px; }
  .store-badges { display: flex; gap: 8px; margin-top: 6px; }
  .store-badge {
    width: 86px; height: 26px; background: var(--ink);
    border: 1px solid var(--badge-edge); border-radius: 4px;
  }

  .schedule {
    position: absolute; left: 300px; top: 672px; width: 340px; height: 116px;
    background: linear-gradient(180deg, var(--white), #dfe3ea);
    border-radius: 26px 0 0 0; color: var(--navy);
    font-family: "Saira", sans-serif; font-size: 13.5px; padding: 10px 18px 0 22px;
  }
  .schedule .heading { text-align: center; font-size: 14px; margin-bottom: 3px; }
  .schedule .row { display: flex; gap: 8px; line-height: 1.25; margin-bottom: 3px; }
  .schedule svg { width: 14px; height: 14px; flex: none; margin-top: 2px; }

  .stripes { position: absolute; left: 300px; top: 800px; width: 340px; }
  .stripes span { display: block; height: 7px; background: var(--white); margin-bottom: 7px; }
  .stripes span.band { background: var(--navy-deep); height: 14px; margin-bottom: 0; }
</style>
</head>
<body>
  <article class="flyer">
    <svg class="flyer-backdrop" viewBox="0 0 640 860" aria-hidden="true">
      <polygon points="0,0 150,0 60,860 0,860" fill="var(--ink)"/>
      <polygon points="150,0 330,0 250,860 60,860" fill="var(--navy-deep)"/>
      <polygon points="330,0 420,0 430,660 330,660" fill="var(--navy-mid)" opacity=".55"/>
      <rect x="0" y="660" width="640" height="200" fill="var(--navy-deep)"/>
    </svg>

    <div class="speaker-photo" role="img" aria-label="Photo of the speaker seated, wearing a royal blue suit and glasses"></div>

    <div class="brand-mark">LUMARA</div>

    <h1 class="event-title">
      <span class="year">Lumen 2025</span>
      <span class="kind">A Prophetic</span>
      <span class="label">Conference</span>
    </h1>

    <h2 class="topic">
      <span class="line"><span class="tag">Topic</span>The Voice</span>
      <span class="line"><span class="outline">Of The</span> Lord</span>
    </h2>

    <div class="speaker-card">
      <p class="role">Speaker</p>
      <p class="name">Prophet Samuel Okoro</p>
    </div>

    <div class="contact">
      <p class="heading">More Info:</p>
      <p class="row"><svg viewBox="0 0 24 24"><path d="M6.6 10.8a15 15 0 0 0 6.6 6.6l2.2-2.2a1 1 0 0 1 1-.25 11.4 11.4 0 0 0 3.6.57 1 1 0 0 1 1 1V20a1 1 0 0 1-1 1A17 17 0 0 1 3 4a1 1 0 0 1 1-1h3.5a1 1 0 0 1 1 1c0 1.25.2 2.45.57 3.57a1 1 0 0 1-.25 1z" fill="var(--white)"/></svg>555 014 2290</p>
      <p class="row"><svg viewBox="0 0 24 24" fill="none" stroke="var(--white)" stroke-width="2"><rect x="3" y="5" width="18" height="14" rx="1"/><path d="M3 6l9 7 9-7"/></svg>hello@lumara.org</p>
      <p class="row"><svg viewBox="0 0 24 24" fill="none" stroke="var(--white)" stroke-width="2"><circle cx="12" cy="12" r="9"/><path d="M3 12h18M12 3a14 14 0 0 1 0 18M12 3a14 14 0 0 0 0 18"/></svg>www.lumara.org</p>
      <p class="app-note">Download the LUMARA App<br>to stay updated on the event</p>
      <div class="store-badges">
        <span class="store-badge"></span>
        <span class="store-badge"></span>
      </div>
    </div>

    <div class="schedule">
      <p class="heading">Date / Time :</p>
      <p class="row"><svg viewBox="0 0 24 24"><path d="M12 2a7 7 0 0 0-7 7c0 5 7 13 7 13s7-8 7-13a7 7 0 0 0-7-7zm0 9.5A2.5 2.5 0 1 1 12 6.5a2.5 2.5 0 0 1 0 5z" fill="var(--navy)"/></svg>The Harborview Arts Hall 120 Maple Lane<br>Riverton, Maine 04000</p>
      <p class="row"><svg viewBox="0 0 24 24" fill="none" stroke="var(--navy)" stroke-width="2"><rect x="3" y="5" width="18" height="16" rx="2"/><path d="M3 10h18M8 3v4M16 3v4"/></svg>Friday December 26th</p>
      <p class="row"><svg viewBox="0 0 24 24" fill="none" stroke="var(--navy)" stroke-width="2"><circle cx="12" cy="12" r="9"/><path d="M12 7v5l3 2"/></svg>6:30PM - 9:00PM</p>
    </div>

    <div class="stripes" aria-hidden="true"><span></span><span></span><span class="band"></span></div>
  </article>
</body>
</html>
```